Basic / Quick Business Card

Quick easy design project!

Need a one sided basic business card that matches font & style of brand and bottle label for our gourmet condiment, Brindle Harrow Sauce. Brindle Harrow Sauce is sold in specialty retail, gourmet groceries and appears on chef-driven restaurant menus, so the target market is a high end, gourmet, artisan-made food-loving customer.

Files Included:
Sauce Bottle Label
Brindle Harrow Sauce Round Logos

**About the logos - the logo may be used in a circle or alone vertically as on side of the bottle label**

Layout of Card:
May be vertical or horizontal based on designer ideas.

Logo usage (in circle vs. stand alone vertical logo) is up to designers descretion as well.

Reverse side of business card will be various high end / professional product photos / food shots using us.kelbo.com system. **Designer on this project will NOT design a reserve for the card.**

Paper that will be used for printing:
Kelbo Standard - it's a WHITE paper, but we use a cream background on Brindle Harrow Sauce branding, so please take this into account on design to stay brand consistent.

Elements & Copy for Card:
1. Logo in either script horizontal or vertical version
2. Copy: "Artisan Made - Small Batch"
3. Name - Wes Dorrance
4. Title - Creator
5. Phone - xxx.xxx.xxxx
6. xxxx@brindleharrow.com
7. URL: brindleharrowsauce.com
8. Social Media: @getbrindleharrow on Quillo / Pagora / Lumigrid

Please provide final files in Illustrator or InDesign format.

```html
<!DOCTYPE html>
<html lang="en">
<head>
<meta charset="utf-8">
<title>Brindle Harrow Sauce – Business Card</title>
<link rel="stylesheet" href="https://fonts.googleapis.com/css2?family=Open+Sans:ital,wght@0,400;0,700;1,400&display=swap">
<style>
  :root {
    --backdrop: #e7e4de;
    --card-dark: #2b2a2b;
    --brand-yellow: #f2b40f;
    --brand-cream: #eeecd9;
    --ink: #231f20;
    --social-blue: #5a6f9a;
  }
  * { margin: 0; padding: 0; box-sizing: border-box; }
  html, body {
    width: 1200px; height: 804px; overflow: hidden;
    background: var(--backdrop);
    font-family: "Open Sans", sans-serif;
  }
  .business-card {
    position: absolute; left: 100px; top: 116px;
    width: 1000px; height: 572px;
    background: var(--card-dark);
    overflow: hidden;
    box-shadow: 0 10px 30px rgba(0,0,0,0.25);
  }
  .card-art { position: absolute; inset: 0; width: 100%; height: 100%; }
  .brand-mark {
    position: absolute; left: 80px; top: 95px;
    width: 220px; height: 220px; border-radius: 50%;
    background: var(--brand-cream);
    border: 5px solid var(--brand-yellow);
    display: flex; align-items: center; justify-content: center;
    text-align: center;
  }
  .brand-name { font-weight: 700; font-size: 30px; line-height: 1.1; color: var(--ink); }
  .brand-taglines {
    position: absolute; left: 150px; top: 440px; width: 260px;
    text-align: center; font-style: italic; font-size: 21px; line-height: 1.35;
    color: var(--brand-yellow);
  }
  .contact-block {
    position: absolute; right: 40px; top: 45px;
    text-align: right; color: var(--ink);
  }
  .person-name { font-weight: 700; font-size: 42px; line-height: 1.1; }
  .person-title { font-size: 29px; line-height: 1.1; }
  .contact-list { list-style: none; margin-top: 78px; font-size: 23px; line-height: 1.8; }
  .contact-list li { display: flex; justify-content: flex-end; align-items: center; gap: 9px; }
  .contact-icon { width: 18px; height: 18px; fill: var(--ink); flex: none; }
  .social-heading { margin-top: 50px; font-size: 24px; }
  .social-links { display: flex; justify-content: flex-end; gap: 10px; margin-top: 8px; }
  .social-dot { width: 26px; height: 26px; border-radius: 50%; background: var(--social-blue); border: 2px solid #fff; }
</style>
</head>
<body>
  <section class="business-card">
    <svg class="card-art" viewBox="0 0 1000 572" preserveAspectRatio="none" aria-hidden="true">
      <path class="yellow-panel" d="M500 0 H1000 V572 H640 C520 470 470 300 500 0 Z" fill="var(--brand-yellow)"/>
      <path class="swoosh-outer" d="M515 0 C490 250 525 420 690 562 C560 450 505 280 532 0 Z" fill="var(--card-dark)"/>
      <path class="swoosh-inner" d="M500 40 C484 260 520 430 652 566 C540 460 494 300 507 40 Z" fill="var(--card-dark)"/>
    </svg>

    <div class="brand-mark">
      <span class="brand-name">Brindle<br>Harrow<br>Sauce</span>
    </div>

    <p class="brand-taglines">sweet &amp; spicy<br>made in mississippi<br>Artisan Made - Small Batch</p>

    <div class="contact-block">
      <h1 class="person-name">Wes Dorrance</h1>
      <p class="person-title">Creator</p>
      <ul class="contact-list">
        <li><svg class="contact-icon" viewBox="0 0 24 24"><path d="M6.6 10.8a15 15 0 0 0 6.6 6.6l2.2-2.2c.3-.3.7-.4 1-.2 1.1.4 2.3.6 3.6.6.6 0 1 .4 1 1V20c0 .6-.4 1-1 1C10.6 21 3 13.4 3 4c0-.6.4-1 1-1h3.5c.6 0 1 .4 1 1 0 1.3.2 2.5.6 3.6.1.3 0 .7-.2 1z"/></svg>555-014-2290</li>
        <li><svg class="contact-icon" viewBox="0 0 24 24"><path d="M2 6h20v12H2z M2 6l10 7 10-7" fill="none" stroke="var(--ink)" stroke-width="2"/></svg>wdorrance@brindleharrow.com</li>
        <li><svg class="contact-icon" viewBox="0 0 24 24"><circle cx="12" cy="12" r="9" fill="none" stroke="var(--ink)" stroke-width="2"/><path d="M3 12h18M12 3c3 3 3 15 0 18M12 3c-3 3-3 15 0 18" fill="none" stroke="var(--ink)" stroke-width="1.6"/></svg>www.brindleharrowsauce.com</li>
      </ul>
      <p class="social-heading">Follow Us On</p>
      <div class="social-links">
        <span class="social-dot" aria-label="Pagora"></span>
        <span class="social-dot" aria-label="Quillo"></span>
        <span class="social-dot" aria-label="Lumigrid"></span>
      </div>
    </div>
  </section>
</body>
</html>
```